Residential Mortgage Leader needs Wordpress Design

Looking for a home page website design for a client. We develop using the WordPress platform and would prefer the design be at least loosely based on an existing WordPress template. Attached files have many notes from our creative brief with client. The site must be responsive. Approved, basic wireframe attached. There is room for interpretation.

Existing web site: http://www.marisolkettering.example/

The Marisol Kettering Team relies on strong systems to deliver an on-time, done-right, friendly experience. Marisol offers mortgages and refinancing services throughout the United States. She is a successful Brookvale Funding agent who strives to be an active part of her community. She would like to focus the site on her team, rather than just her.

Difference makers...
When you work with the Marisol Kettering team you get a high level of expertise and a friendly experience.

She has amazing credentials. Marisol is widely recognized as a top producer for her company, and has earned a number of awards and honors for her customer service.

Marisol's team is very engaged and enjoys sharing social comments or photos from their community.

Imagery:
* Friendly, warm imagery, preferably of her team or an image to represent her team
* Clean and crisp
* Professional / Experts in mortgage and refinance
* Clean / Good use of white space
Updates

When possible, please use imagery from the DFW area. The client mentioned they would prefer not to see stock images. Thanks.

Amend that- creative use of stock images, however, is fine. A few designs have used stock imagery, but in a well-considered manner.

We added some photos and graphics that are local. We are Dallas / Ft. Worth, Plano, Frisco, Texas. We also added some examples of photos to use for the "In the Community" area. Stock photos of business folks just doesn't fit there. Thanks!

Target Market(s)

They service a lot of builders, but also work with homeowners. Their typical client is usually a woman searching for mortgage services online. She typically has a family and may refer her husband to Marisol's team. Keep in mind, however, they also see a number of other scenarios. Most of their clients are middle to high-end borrowers.

Industry/Entity Type

It Company

Requirements
Must have
• Design should be developed using program such as Photoshop or Fireworks or Illustrator as last preference. Ideally, the design would be based on an existing responsive WordPress theme, which we would customize. You must include the name of the target theme. The footer should include lots of space for disclaimers and legal language. Site navigation should include these choices: "Home, About, Builders, Mortgage Info, Approval, Blog, Contact"
Nice to have
• Blog, social media and photos area. Use of the already approved style prototype with colors and fonts (Lato- a Google font, Times New Roman and Cookie-a decorative Google font). However, we are open to interpretation.
Should not have
• Hard to read fonts or a lack of white space.

```html
<!DOCTYPE html>
<html lang="en">
<head>
<meta charset="utf-8">
<title>Marisol Kettering Team — Home</title>
<link href="https://fonts.googleapis.com/css2?family=Lato:wght@300;400;700;900&family=Cookie&family=Tinos:wght@400;700&display=swap" rel="stylesheet">
<style>
:root{
  --red:#c9170f;
  --blue:#1b8fc4;
  --ink:#333333;
  --muted:#7a7a7a;
  --rule:#e4e4e4;
  --panel:#f4f4f4;
  --footer:#363636;
  --footer-text:#cfcfcf;
  --nav-top:#444444;
  --nav-bot:#262626;
}
*{box-sizing:border-box;margin:0;padding:0}
html,body{width:889px;height:1200px;overflow:hidden;background:#fff}
body{font-family:"Lato",sans-serif;color:var(--ink)}
.page{position:relative;width:889px;height:1200px;overflow:hidden}
.abs{position:absolute}
ul{list-style:none}

/* top bar */
.topbar{left:0;top:0;width:889px;height:27px;background:var(--red)}
.topbar .label{position:absolute;left:587px;top:8px;font-size:8.5px;font-weight:900;color:#fff;letter-spacing:-.2px}
.topbar .dots{position:absolute;left:669px;top:8px;display:flex;gap:7px}
.topbar .dots span{width:10px;height:10px;border-radius:50%;background:#fff}

/* header */
.brand{left:148px;top:44px;width:124px}
.brand-name{display:block;font-family:"Tinos","Times New Roman",serif;font-size:18px;letter-spacing:-.2px;color:var(--red);line-height:1;white-space:nowrap}
.brand-tag{display:block;text-align:right;margin-top:2px;font-size:5px;letter-spacing:.4px;color:#9a9a9a;white-space:nowrap}
.brand-divider{left:279px;top:44px;width:1px;height:28px;background:#ddd}
.partner{left:287px;top:49px}
.partner-name{display:flex;align-items:center;gap:5px;font-size:11px;font-weight:900;color:var(--red);white-space:nowrap}
.partner-name i{width:9px;height:9px;border-radius:50%;background:var(--red);display:block}
.partner-sub{font-size:5px;color:#555;margin-top:2px;white-space:nowrap}
.work{right:148px;top:37px;text-align:right}
.work h4{font-family:"Tinos","Times New Roman",serif;font-size:12px;font-weight:700;letter-spacing:.3px;color:#222}
.work .phone{font-size:12px;font-weight:700;color:var(--red);letter-spacing:1px;margin-top:1px}
.work .mail{display:flex;align-items:center;justify-content:flex-end;gap:5px;margin-top:5px;font-size:7px;font-weight:700;color:var(--red)}
.work .mail span.sep{color:#aaa;font-weight:400}

/* nav */
.nav{left:0;top:85px;width:889px;height:35px;background:linear-gradient(var(--nav-top),var(--nav-bot));border-top:1px solid #1d1d1d}
.nav ul{position:absolute;left:140px;top:0;display:flex;height:34px}
.nav li{font-size:9.5px;font-weight:700;color:#fff;padding:0 14px;line-height:34px;border-right:1px solid #1c1c1c;box-shadow:1px 0 0 #4e4e4e}
.nav li:last-child{border:0;box-shadow:none}
.search{position:absolute;left:582px;top:7px;width:159px;height:21px;display:flex}
.search .field{flex:1;background:#fff;font-size:5px;color:#bbb;padding:0 10px;line-height:21px}
.search .go{width:29px;background:var(--red);display:flex;align-items:center;justify-content:center}

/* hero */
.hero{left:0;top:120px;width:889px;height:250px;background:linear-gradient(180deg,#d9e9f3 0%,#eef5fa 65%,#e3edf4 100%)}
.hero-photo{position:absolute;left:130px;top:12px;width:312px;height:238px;background:linear-gradient(180deg,#b9c3cc 0%,#6f6a6a 45%,#2d2d33 100%);border-radius:6px 6px 0 0}
.hero h1{position:absolute;left:455px;top:44px;font-family:"Cookie",cursive;font-weight:400;font-size:45px;color:var(--red);line-height:1;white-space:nowrap}
.hero p{position:absolute;left:457px;top:112px;width:270px;font-size:11.5px;font-weight:300;line-height:21px;color:#4a4a4a}
.hero .cta{position:absolute;left:456px;top:182px;display:flex;align-items:center;gap:8px}
.btn{width:92px;height:25px;background:var(--blue);color:#fff;font-size:10px;font-weight:900;text-align:center;line-height:25px;border-radius:2px}
.cta .or{font-size:9px;color:#999}
.cta a{font-size:11px;color:var(--red);text-decoration:none}

/* credentials */
.cred-band{left:0;top:417px;width:889px;height:17px;background:var(--red)}
.cred-title{left:144px;top:398px;width:216px;height:50px;background:#fff;font-family:"Cookie",cursive;font-weight:400;font-size:42px;color:var(--blue);text-align:center;line-height:50px}
.cred{top:460px;font-size:10.4px;font-weight:300;color:#555;line-height:13px}
.cred h3{font-family:"Tinos","Times New Roman",serif;font-weight:700;color:var(--red);display:inline-block;border-bottom:1px dotted var(--red);padding-bottom:2px;margin-bottom:4px}
.cred .more{display:block;margin-top:4px;font-size:7px;font-weight:700;color:var(--red)}
.cred-main{left:149px;width:240px}
.cred-main h3{font-size:14.5px}
.cred-side{width:150px}
.cred-side h3{font-size:13px;margin-left:38px}
.cred-side .badge{position:absolute;left:0;top:0;width:28px;height:28px;border-radius:50%;background:#2b3e58;display:flex;align-items:center;justify-content:center}
.cred-side p{margin-top:8px}
.vrule{width:1px;height:62px;background:#e4e4e4;top:476px}

/* community */
.community{left:0;top:563px;width:889px;height:323px;background:var(--panel)}
.community h2{position:absolute;left:0;width:889px;top:16px;text-align:center;font-family:"Cookie",cursive;font-weight:400;font-size:40px;color:var(--blue)}
.community .sub{position:absolute;left:280px;width:329px;top:62px;display:flex;align-items:center;gap:8px;font-size:16px;font-weight:300;color:var(--red);white-space:nowrap}
.sub i{flex:1;border-top:2px dotted #a9cde3}
.card{top:109px;width:181px;height:175px;background:#fff;box-shadow:0 0 3px rgba(0,0,0,.08)}
.card h4{font-family:"Tinos","Times New Roman",serif;font-weight:400;font-size:14px;color:#222;padding:9px 11px 7px;border-bottom:1px solid var(--rule)}
.card h4 b{color:var(--red)}
.blogs li{display:flex;align-items:center;gap:6px;height:23.7px;margin:0 4px;padding:0 8px 0 10px;border-bottom:1px solid #eee;font-size:10px;font-weight:300;color:var(--blue)}
.blogs li::before{content:"";width:4px;height:4px;border-radius:50%;background:var(--red);flex:none}
.blogs li::after{content:"";flex:1;border-top:1px dotted #ccc;margin-left:4px}
.blogs li:last-child{border:0}
.post{display:flex;gap:10px;padding:7px 10px 6px 12px;border-bottom:1px solid #eee;height:43px}
.post:last-child{border:0}
.thumb{width:42px;height:32px;flex:none;background:linear-gradient(135deg,#8a7a6e,#3d3a3d)}
.post .head{display:flex;align-items:baseline;gap:3px;font-size:7.5px;font-weight:900;color:var(--blue)}
.post .head .d{font-size:10px;color:var(--red);margin-left:3px}
.post .head .m{font-size:5.5px;color:var(--red)}
.post .head .ic{width:6px;height:6px;border-radius:50%;background:var(--blue);margin-left:3px;align-self:center}
.post p{font-size:5px;line-height:6.5px;color:#999;margin-top:2px}
.gallery{display:grid;grid-template-columns:repeat(2,77px);gap:7px 10px;padding:13px 10px}
.gallery figure{height:58px}
.gallery .ph{width:73px;height:42px;border:2px solid #fff;box-shadow:0 0 2px rgba(0,0,0,.25);background:linear-gradient(160deg,#b58a5a,#3a2a22)}
.gallery figcaption{font-size:7.2px;color:var(--blue);margin-top:3px;letter-spacing:-.2px}

/* footer */
.footer{left:0;top:886px;width:889px;height:314px;background:var(--footer);color:var(--footer-text)}
.fhead{position:absolute;display:flex;align-items:center;gap:8px;font-size:11.5px;color:#fff;font-weight:400;letter-spacing:-.2px}
.fhead::before{content:"";width:14px;height:2px;background:var(--blue)}
.fhead::after{content:"";width:62px;height:1px;background:#8a8a8a}
.photos{position:absolute;left:149px;top:68px}
.photos li{display:flex;gap:10px;height:48px}
.photos .tn{width:36px;height:36px;background:linear-gradient(135deg,#5a6a72,#1c2126)}
.photos h5{font-size:9px;font-weight:400;color:#fff}
.photos span{display:block;font-size:7.5px;color:#aaa;line-height:11px}
.links{position:absolute;width:146px}
.links li{font-size:8.5px;font-weight:300;color:#bdbdbd;height:19.7px;line-height:17px;border-bottom:1px solid #424242;letter-spacing:-.2px}
.addr{position:absolute;top:241px;display:grid;grid-template-columns:14px 1fr;gap:2px 4px;font-size:7.5px;color:#bbb;line-height:9px}
.addr b{color:#fff;font-weight:700}
.addr svg{margin-top:1px}
.copy{position:absolute;right:146px;top:285px;font-size:8.5px;font-weight:300;color:#bdbdbd}
</style>
</head>
<body>
<div class="page">

  <div class="abs topbar">
    <span class="label">CONNECT WITH US:</span>
    <div class="dots" aria-label="Social profiles"><span></span><span></span><span></span><span></span><span></span></div>
  </div>

  <header>
    <div class="abs brand">
      <span class="brand-name">marisolkettering</span>
      <span class="brand-tag">THE MARISOL KETTERING TEAM</span>
    </div>
    <div class="abs brand-divider"></div>
    <div class="abs partner">
      <div class="partner-name">Brookvale Funding <i></i></div>
      <div class="partner-sub">A Cedarline Capital Company.</div>
    </div>
    <div class="abs work">
      <h4>WORK WITH US</h4>
      <div class="phone">214-555-0147</div>
      <div class="mail">
        <svg width="10" height="7" viewBox="0 0 10 7"><rect width="10" height="7" fill="#333"/><path d="M0 0l5 4 5-4" stroke="#fff" fill="none"/></svg>
        <span class="sep">|</span> EMAIL@MARISOLKETTERING.EXAMPLE
      </div>
    </div>
  </header>

  <nav class="abs nav">
    <ul>
      <li>Home</li><li>About</li><li>Builders</li><li>Mortgage Info</li><li>Approval</li><li>Blog</li><li>Contact</li>
    </ul>
    <div class="search">
      <div class="field">TYPE YOUR KEYWORDS HERE</div>
      <div class="go"><svg width="12" height="12" viewBox="0 0 12 12"><circle cx="7" cy="5" r="3.5" stroke="#fff" stroke-width="1.8" fill="none"/><path d="M4.5 7.5L1 11" stroke="#fff" stroke-width="2"/></svg></div>
    </div>
  </nav>

  <section class="abs hero">
    <div class="hero-photo" role="img" aria-label="Photo of the mortgage team in business attire standing together, city skyline behind"></div>
    <h1>Earning Your Business</h1>
    <p>The Marisol Kettering Team Relies On Strong System To Deliever An On Time Done Right And Friendly Experience .</p>
    <div class="cta"><div class="btn">START HERE</div><span class="or">-OR-</span><a href="#">Get to know us</a></div>
  </section>

  <section>
    <div class="abs cred-band"></div>
    <h2 class="abs cred-title">Our Credentials</h2>
    <div class="abs cred cred-main">
      <h3>Lorem Ipsum Dolor Sit Amet.</h3>
      <p>Lorem ipsum dolor sit amet, consectetuer adipiscing elit, sed diam nonummy nibh euismod tincidunt ut laoreet dolore magna aliquam erat volutpat.</p>
      <span class="more">Read More &gt;&gt;</span>
    </div>
    <div class="abs vrule" style="left:400px"></div>
    <div class="abs cred cred-side" style="left:416px">
      <div class="badge"><svg width="14" height="14" viewBox="0 0 14 14"><path d="M3 1h8v4a4 4 0 0 1-8 0z" fill="#f2b41c"/><rect x="6" y="8" width="2" height="3" fill="#f2b41c"/><rect x="4" y="11" width="6" height="2" fill="#f2b41c"/></svg></div>
      <h3>Awards</h3>
      <p>Lorem ipsum dolor sit amet, consectetuer adipiscing elit, sed diam nonummy nibh euismod.</p>
      <span class="more">Read More &gt;&gt;</span>
    </div>
    <div class="abs vrule" style="left:578px"></div>
    <div class="abs cred cred-side" style="left:592px;top:458px">
      <div class="badge"><svg width="14" height="14" viewBox="0 0 14 14"><rect x="1" y="6" width="3" height="7" fill="#fff"/><path d="M5 6l3-5c1 0 2 1 1.5 3H13v2l-2 7H5z" fill="#f2c28a"/></svg></div>
      <h3>Recognition</h3>
      <p>Lorem ipsum dolor sit amet, consectetuer adipiscing elit, sed diam nonummy nibh euismod.</p>
      <span class="more">Read More &gt;&gt;</span>
    </div>
  </section>

  <section class="abs community">
    <h2>Engaged In Our Community</h2>
    <div class="sub"><i></i>Connect With Us<i></i></div>

    <div class="abs card" style="left:147px">
      <h4>Our <b>Blogs</b></h4>
      <ul class="blogs">
        <li>Borrowing</li><li>Best Practices</li><li>Annoucements</li><li>Resources</li><li>How To Guides</li><li>Building Info</li>
      </ul>
    </div>

    <div class="abs card" style="left:353px">
      <h4>Social <b>Media</b></h4>
      <div class="post"><div class="thumb" role="img" aria-label="Profile photo"></div><div><div class="head">LOREM IPSUM <span class="d">2</span><span class="m">MARCH</span><span class="ic"></span></div><p>Lorem ipsum dolor sit amet, consectetuer adipiscing elit dolor sit amet, consectetuer adipiscing elit.</p></div></div>
      <div class="post"><div class="thumb" role="img" aria-label="Profile photo"></div><div><div class="head">LOREM IPSUM <span class="d">2</span><span class="m">MARCH</span><span class="ic"></span></div><p>Lorem ipsum dolor sit amet, consectetuer adipiscing elit dolor sit amet, consectetuer adipiscing elit.</p></div></div>
      <div class="post"><div class="thumb" role="img" aria-label="Profile photo"></div><div><div class="head">LOREM IPSUM <span class="d">2</span><span class="m">MARCH</span><span class="ic"></span></div><p>Lorem ipsum dolor sit amet, consectetuer adipiscing elit dolor sit amet, consectetuer adipiscing elit.</p></div></div>
    </div>

    <div class="abs card" style="left:558px">
      <h4>In the <b>Community</b></h4>
      <div class="gallery">
        <figure><div class="ph" role="img" aria-label="Photo of a community banquet event"></div><figcaption>Lorem Ipsum Dolor.</figcaption></figure>
        <figure><div class="ph" role="img" aria-label="Photo of a speaker at a community gathering"></div><figcaption>Lectors Ipsum Dolor.</figcaption></figure>
        <figure><div class="ph" role="img" aria-label="Photo of a crowded community hall"></div><figcaption>Jordan Ipsum Dolor.</figcaption></figure>
        <figure><div class="ph" role="img" aria-label="Photo of guests seated at a dinner event"></div><figcaption>Union Ipsum Dolor.</figcaption></figure>
      </div>
    </div>
  </section>

  <footer class="abs footer">
    <h5 class="fhead" style="left:149px;top:40px">LATEST PHOTOS</h5>
    <ul class="photos">
      <li><div class="tn" role="img" aria-label="Thumbnail photo"></div><div><h5>Standard post format</h5><span>June 12, 2013</span><span>NMLS # 480317</span></div></li>
      <li><div class="tn" role="img" aria-label="Thumbnail photo"></div><div><h5>Big Bunny Video Clip</h5><span>June 12, 2013</span><span>NMLS # 480317</span></div></li>
      <li><div class="tn" role="img" aria-label="Thumbnail photo"></div><div><h5>Post With Slider</h5><span>June 12, 2013</span><span>NMLS # 480317</span></div></li>
    </ul>

    <h5 class="fhead" style="left:385px;top:40px">LINKS</h5>
    <ul class="links" style="left:386px;top:62px">
      <li>Styling Options</li><li>General Options</li><li>Overview</li><li>header Settings</li><li>Showcase</li><li>Website Design</li><li>Layout</li>
    </ul>

    <h5 class="fhead" style="left:594px;top:40px">MISC LANGUAGE</h5>
    <ul class="links" style="left:595px;top:62px;width:137px">
      <li>American Indian Pidgin English</li><li>Chinese Pidgin English</li><li>Hawaiian Pidgin English</li><li>Japanese Bamboo English</li><li>Japanese Pidgin English</li><li>Korean Bamboo English</li><li>Kru Pidgin English</li><li>Liberian Interior Pidgin English</li>
    </ul>

    <h5 class="fhead" style="left:149px;top:218px">ADDERESS</h5>
    <div class="addr" style="left:150px">
      <svg width="12" height="11" viewBox="0 0 12 11"><path d="M6 0L0 5h2v6h8V5h2z" fill="#ddd"/></svg><b>Alder Court - 4820 Alder Court ,<br>Ste. 210 . Frisco, TX 75099</b>
      <svg width="12" height="11" viewBox="0 0 12 11"><path d="M2 1l3 1-1 2 3 3 2-1 1 3-2 1C4 10 1 6 1 3z" fill="#ddd"/></svg><span>Tel : 469.555.0182<br>Fax : 866.555.0139</span>
      <svg width="12" height="9" viewBox="0 0 12 9"><rect width="12" height="9" fill="#ddd"/><path d="M0 0l6 5 6-5" stroke="#363636" fill="none"/></svg><span>Email : Contact Marisol Kettering</span>
    </div>
    <div class="addr" style="left:317px">
      <svg width="12" height="11" viewBox="0 0 12 11"><path d="M6 0L0 5h2v6h8V5h2z" fill="#ddd"/></svg><b>Corporate Office - 7400 Harwell<br>Road, Suite 600 Dallas, Texas 75299</b>
      <svg width="12" height="11" viewBox="0 0 12 11"><path d="M2 1l3 1-1 2 3 3 2-1 1 3-2 1C4 10 1 6 1 3z" fill="#ddd"/></svg><span>Tel : 1-800-555-0163<br>&nbsp;</span>
      <svg width="12" height="9" viewBox="0 0 12 9"><rect width="12" height="9" fill="#ddd"/><path d="M0 0l6 5 6-5" stroke="#363636" fill="none"/></svg><span>Email : Contact Brookvale Funding</span>
    </div>
    <p class="copy">Copyright 2013 By Marisol Kettering. All Rights Reserved.</p>
  </footer>

</div>
</body>
</html>
```